Corporate Design für Hausverwalterin und Immobilienvermarktung
Zielgruppe
Hausverwalterin und Immobilienvermarktung
Aufgabenstellung
wir sind im Immobiliensektor unterwegs und das Design soll edel und hochwertig sein

```html
<!DOCTYPE html>
<html lang="de">
<head>
<meta charset="utf-8">
<title>Marlen Immobilien – Corporate Design</title>
<link rel="stylesheet" href="https://fonts.googleapis.com/css2?family=Tinos&family=Arimo:ital,wght@0,400;0,700;1,700&display=swap">
<style>
  :root{
    --navy:#152c42;
    --navy-deep:#0c2035;
    --gold:#b08d4a;
    --paper:#ffffff;
    --stage:#e8e9eb;
    --ink:#1d2b3a;
    --window:#e4e4e4;
  }
  *{margin:0;padding:0;box-sizing:border-box}
  html,body{width:1200px;height:2399px;overflow:hidden}
  body{position:relative;background:var(--paper);font-family:"Arimo",Arial,sans-serif}
  .abs{position:absolute}

  /* wordmark */
  .wordmark{display:inline-flex;align-items:center;gap:.35em;font-family:"Tinos","Times New Roman",serif;color:var(--gold);font-weight:400;white-space:nowrap;line-height:1}
  .wordmark .mark{width:.55em;height:.55em;background:var(--gold);display:inline-block}

  /* stage */
  .stage{left:0;top:0;width:1200px;height:798px;background:var(--stage)}
  .card-lg{width:440px;height:284px;background:var(--navy-deep);top:257px;display:flex;align-items:center;justify-content:center;text-align:center}
  .card-lg.back{left:120px}
  .card-lg.front{left:640px}
  .card-lg .wordmark{font-size:36px}

  .card-text{color:#fff;font-size:11.5px;line-height:1.32}
  .card-text p+p{margin-top:.75em}
  .card-text .services{font-weight:700;font-style:italic}
  .card-text.on-light{color:var(--gold)}

  /* logo panels */
  .panel{top:798px;width:600px;height:400px;display:flex;align-items:center;justify-content:center}
  .panel.light{left:0;background:var(--paper)}
  .panel.dark{left:600px;background:var(--navy)}
  .panel .wordmark{font-size:40px}

  /* stationery board */
  .board{left:0;top:1198px;width:1200px;height:1201px;background:var(--navy)}
  .sheet{left:21px;top:1220px;width:1157px;height:1157px;background:var(--paper)}
  .item{box-shadow:2px 4px 6px rgba(0,0,0,.28)}

  .card-sm{width:203px;height:130px;top:1285px;display:flex;align-items:center;justify-content:center;text-align:center}
  .card-sm.dark{background:var(--navy)}
  .card-sm.light{background:var(--paper)}
  .card-sm .wordmark{font-size:15px}
  .card-sm .card-text{font-size:5.4px}

  .letter{width:425px;height:601px;top:1452px;background:var(--paper)}
  .letter .wordmark{position:absolute;left:40px;top:60px;font-size:12px}
  .letter-foot{position:absolute;left:46px;bottom:26px;display:flex;gap:12px;font-size:4.8px;line-height:1.3;color:var(--ink)}
  .letter-foot div{padding-right:10px}
  .letter-foot div+div{border-left:.6px solid var(--gold);padding-left:8px}
  .sender{position:absolute;left:296px;top:28px;border-left:.6px solid var(--ink);padding-left:10px;font-size:4.8px;line-height:1.3;color:var(--ink)}
  .sender p+p{margin-top:5px}
  .return-line{position:absolute;left:37px;top:96px;font-size:4.6px;color:var(--ink)}

  .envelope{width:425px;height:212px;top:2084px;background:var(--paper)}
  .envelope .wordmark{position:absolute;left:50px;top:26px;font-size:14px}
  .env-window{position:absolute;left:29px;top:108px;width:145px;height:71px;background:var(--window);border-radius:8px}
  .env-flap{position:absolute;left:0;top:0}
  .envelope.back .wordmark{left:50%;transform:translateX(-50%);top:28px;font-size:12px}
</style>
</head>
<body>

<section class="abs stage">
  <div class="abs card-lg back">
    <div class="card-text">
      <p>Ganzheitliche Immobilienbetreuung mit Strategie.</p>
      <p>Als zertifizierte Hausverwalterin &amp; Immobilienmaklerin<br>gemäß § 34c GewO verbinde ich klassische Verwaltung<br>mit wertoptimierter Vermarktung:</p>
      <p class="services">- Hausverwaltung: Rechtssicher &amp; entlastend.<br>- Asset Management: Strategische Ertragssteigerung.<br>- Verkauf: Marktgerecht &amp; professionell.</p>
      <p>Marlen Immobilien - Ihr Eigentum in zuverlässigen Händen.</p>
      <p>Telefon: 0171 386 42 19<br>E-Mail: info@marlen-immobilien.de<br>Webseite: www.marlen-immobilien.de</p>
    </div>
  </div>
  <div class="abs card-lg front">
    <span class="wordmark"><span class="mark"></span>Marlen Immobilien</span>
  </div>
</section>

<section class="abs panel light">
  <span class="wordmark"><span class="mark"></span>Marlen Immobilien</span>
</section>
<section class="abs panel dark">
  <span class="wordmark"><span class="mark"></span>Marlen Immobilien</span>
</section>

<section class="abs board"></section>
<section class="abs sheet"></section>

<div class="abs item card-sm dark" style="left:133px">
  <span class="wordmark"><span class="mark"></span>Marlen Immobilien</span>
</div>
<div class="abs item card-sm dark" style="left:355px">
  <div class="card-text">
    <p>Ganzheitliche Immobilienbetreuung mit Strategie.</p>
    <p>Als zertifizierte Hausverwalterin &amp; Immobilienmaklerin<br>gemäß § 34c GewO verbinde ich klassische Verwaltung<br>mit wertoptimierter Vermarktung:</p>
    <p class="services">- Hausverwaltung: Rechtssicher &amp; entlastend.<br>- Asset Management: Strategische Ertragssteigerung.<br>- Verkauf: Marktgerecht &amp; professionell.</p>
    <p>Marlen Immobilien - Ihr Eigentum in zuverlässigen Händen.</p>
    <p>Telefon: 0171 386 42 19<br>E-Mail: info@marlen-immobilien.de<br>Webseite: www.marlen-immobilien.de</p>
  </div>
</div>
<div class="abs item card-sm light" style="left:610px">
  <span class="wordmark"><span class="mark"></span>Marlen Immobilien</span>
</div>
<div class="abs item card-sm light" style="left:831px">
  <div class="card-text on-light">
    <p>Ganzheitliche Immobilienbetreuung mit Strategie.</p>
    <p>Als zertifizierte Hausverwalterin &amp; Immobilienmaklerin<br>gemäß § 34c GewO verbinde ich klassische Verwaltung<br>mit wertoptimierter Vermarktung:</p>
    <p class="services">- Hausverwaltung: Rechtssicher &amp; entlastend.<br>- Asset Management: Strategische Ertragssteigerung.<br>- Verkauf: Marktgerecht &amp; professionell.</p>
    <p>Marlen Immobilien - Ihr Eigentum in zuverlässigen Händen.</p>
    <p>Telefon: 0171 386 42 19<br>E-Mail: info@marlen-immobilien.de<br>Webseite: www.marlen-immobilien.de</p>
  </div>
</div>

<div class="abs item letter" style="left:133px">
  <span class="wordmark"><span class="mark"></span>Marlen Immobilien</span>
  <div class="letter-foot">
    <div>Morelotix<br>Marlen Immobilien Verwaltung &amp; Vermarktung<br>Germany 01 0000 Germany</div>
    <div>Telefon: 0171 386 42 19<br>E-Mail: info@marlen-immobilien.de<br>Webseite: www.marlen-immobilien.de</div>
    <div>Bankverbindung: Kreisbank Nord<br>IBAN XXXX XXXX XXXX XXXX XXXX<br>BIC 12345ABCDEF</div>
  </div>
</div>

<div class="abs item letter" style="left:610px">
  <span class="wordmark"><span class="mark"></span>Marlen Immobilien</span>
  <div class="sender">
    <p>Morelotix<br>Marlen Immobilien<br>Verwaltung &amp; Vermarktung<br>Germany 01<br>0000 Germany</p>
    <p>Telefon: 0171 386 42 19<br>E-Mail: info@marlen-immobilien.de<br>Webseite: www.marlen-immobilien.de</p>
  </div>
  <div class="return-line">Morelotix | Marlen Immobilien Verwaltung &amp; Vermarktung | Germany 01 | 0000 Germany</div>
</div>

<div class="abs item envelope" style="left:133px">
  <span class="wordmark"><span class="mark"></span>Marlen Immobilien</span>
  <div class="env-window"></div>
</div>

<div class="abs item envelope back" style="left:610px">
  <svg class="env-flap" width="425" height="75" viewBox="0 0 425 75">
    <path d="M0 0 H425 L405 60 Q400 75 385 75 H40 Q25 75 20 60 Z" fill="var(--navy)"/>
  </svg>
  <span class="wordmark"><span class="mark"></span>Marlen Immobilien</span>
</div>

</body>
</html>
```